Business Card Design

Need a new business card to represent our legal vertical focus. attached is an example of our old business card and newest logo. we would like the card to also identify "Legal Tech" as a tag line of business.

Our new address is
4817 Marlowe Hatchfield Rd.
Suite 518
Cincinnati, OH 45917

we no longer have a fax number.

Target Market(s)

Tech Consulting for Law Firms

Industry/Entity Type

Legal

Contact Information for Business Card

should use logo and colors. we are a b2b company

Font styles to use
Other font styles liked:
• tahoma

Requirements
Must have
• all print should be in lower case just as shown in photos. tag line should not
Should not have
• pinstripes or drop shadows

```html
<!DOCTYPE html>
<html lang="en">
<head>
<meta charset="utf-8">
<title>kestrellink business card</title>
<link rel="stylesheet" href="https://fonts.googleapis.com/css2?family=Raleway:wght@400;500;700&family=PT+Sans&display=swap">
<style>
  :root {
    --backdrop: #0b0b0c;
    --card-top: #36373b;
    --card-bottom: #2e2f33;
    --accent: #e8512a;
    --brand-blue: #26408f;
    --text-light: #e4e4e4;
    --text-muted: #9b9c9f;
    --tagline: #8e8f93;
  }
  html, body {
    margin: 0;
    padding: 0;
    width: 1200px;
    height: 900px;
    overflow: hidden;
    background: var(--backdrop);
  }
  .canvas {
    position: relative;
    width: 1200px;
    height: 900px;
    font-family: "Raleway", sans-serif;
  }
  .card {
    position: absolute;
    top: 297px;
    height: 280px;
    border-radius: 14px;
    background: linear-gradient(180deg, var(--card-top), var(--card-bottom));
  }
  .card--front { left: 114px; width: 480px; }
  .card--back { left: 629px; width: 483px; }

  .front-mark {
    position: absolute;
    left: 40px;
    top: 110px;
    display: flex;
    align-items: center;
    gap: 10px;
  }
  .front-mark__dot {
    width: 16px;
    height: 16px;
    border-radius: 50%;
    background: var(--accent);
  }
  .front-mark__name {
    font-weight: 700;
    font-size: 24px;
    color: var(--accent);
    letter-spacing: 0.2px;
  }

  .contact {
    position: absolute;
    left: 230px;
    top: 70px;
    color: var(--text-light);
  }
  .contact__name {
    margin: 0;
    font-size: 21px;
    font-weight: 400;
    color: var(--accent);
    line-height: 26px;
  }
  .contact__role {
    margin: 0 0 0 2px;
    font-size: 15px;
    color: var(--text-muted);
    line-height: 18px;
  }
  .contact__lines {
    margin: 18px 0 0 4px;
    font-size: 15px;
    line-height: 18px;
  }
  .contact__label { color: var(--accent); }
  .contact__address {
    margin: 14px 0 0 4px;
    font-size: 15px;
    line-height: 18px;
  }

  .back-logo {
    position: absolute;
    right: 62px;
    top: 98px;
    text-align: right;
  }
  .back-logo__row {
    display: flex;
    align-items: center;
    justify-content: flex-end;
    gap: 14px;
  }
  .back-logo__dot {
    width: 26px;
    height: 26px;
    border-radius: 50%;
    background: var(--accent);
  }
  .back-logo__name {
    font-family: "Raleway", sans-serif;
    font-weight: 700;
    font-size: 50px;
    line-height: 58px;
    color: var(--brand-blue);
  }
  .back-logo__tagline {
    margin-top: 2px;
    font-family: "PT Sans", "Tahoma", sans-serif;
    font-size: 19px;
    letter-spacing: 0.6px;
    color: var(--tagline);
  }
</style>
</head>
<body>
<main class="canvas">
  <section class="card card--front" aria-label="card front">
    <div class="front-mark">
      <span class="front-mark__dot"></span>
      <span class="front-mark__name">kestrellink</span>
    </div>
    <div class="contact">
      <p class="contact__name">marcus hale</p>
      <p class="contact__role">managing director</p>
      <p class="contact__lines">
        <span class="contact__label">e:</span> info@kestrellink.com<br>
        <span class="contact__label">t:</span> 513-555 0148
      </p>
      <p class="contact__address">
        4817 marlowe hatchfield rd., suite 518<br>
        cincinnati, oh 45917
      </p>
    </div>
  </section>

  <section class="card card--back" aria-label="card back">
    <div class="back-logo">
      <div class="back-logo__row">
        <span class="back-logo__dot"></span>
        <span class="back-logo__name">kestrellink</span>
      </div>
      <div class="back-logo__tagline">Legal Tech</div>
    </div>
  </section>
</main>
</body>
</html>
```